Broschüre für Anbieter von Haushaltshilfen und Alltagsbegleitern für Privathaushalte
Zielgruppe
Wir bieten Haushaltshilfen und Alltagsbegleiter für Privathaushalte an. Unsere Hauptkundenklientel sind Pflegebedürftige Menschen denen eine Haushaltshilfe von der Pflegekasse zusteht. Weitere Kunden sind Familien und/oder Singlehaushalte, die eine Haushaltfshilfe benötigen.
Aufgabenstellung
- Das Prospekt sollte DIN A4 sein, sind aber auch offen für andere Formate
- Farbdesign muß unsere Logofarben enthalten
- In dem Prospekt müßen unsere Leistungen wie auf unserer Internetseite www.wolkenmut.de beschrieben sein.
- Seitenanzahl insgesamt 4 Seiten

```html
<!DOCTYPE html>
<html lang="de">
<head>
<meta charset="utf-8">
<title>Wolkenmut Broschüre</title>
<link href="https://fonts.googleapis.com/css2?family=Montserrat:wght@600;700;800&family=Open+Sans:wght@400;600;700&display=swap" rel="stylesheet">
<style>
:root{
  --red:#c8102e;
  --red-dark:#b00d26;
  --ink:#1d1d1f;
  --text:#4a4a4a;
  --paper:#ffffff;
  --paper-grey:#f1f1f3;
  --stage:#e6e6e8;
  --bar:#232325;
}
*{margin:0;padding:0;box-sizing:border-box}
html,body{width:1200px;height:3567px;overflow:hidden;background:var(--stage)}
body{position:relative;font-family:"Open Sans",sans-serif}
.spread{position:absolute;left:50px;width:1100px;height:768px;display:flex;box-shadow:0 10px 30px rgba(0,0,0,.12)}
.spread--outer{top:975px}
.spread--inner{top:1823px}
.page{position:relative;width:550px;height:768px;overflow:hidden}
.page + .page{border-left:1px solid #d7d7da}
.brand{position:absolute;display:flex;align-items:center;gap:8px;font-family:"Montserrat",sans-serif;font-weight:700;font-size:19px;letter-spacing:.5px}
.brand__dot{width:22px;height:22px;border-radius:50%;border:2px solid currentColor}
.brand--light{color:#fff}
.brand--red{color:var(--red)}
.heading{font-family:"Montserrat",sans-serif;font-weight:800;line-height:1.12}
.url{position:absolute;bottom:34px;font-size:10px}
.end-line{position:absolute;bottom:40px;right:40px;width:40px;height:1px}
.photo{position:absolute}

/* outer spread — back cover */
.back{background:var(--red-dark)}
.back__card{position:absolute;left:0;top:0;width:512px;height:690px;background:var(--red);border-bottom-right-radius:26px}
.back__bar{position:absolute;left:512px;top:0;width:12px;height:125px;background:var(--bar)}
.back .brand{left:38px;top:28px}
.back__title{position:absolute;left:38px;top:120px;color:#fff;font-size:41px}
.back__dash{position:absolute;left:38px;top:282px;width:38px;height:3px;background:#fff}
.contact{position:absolute;left:38px;top:555px;width:436px;color:#fff}
.contact__name{font-weight:700;font-size:12.5px;line-height:1.55}
.contact__rule{height:1px;background:rgba(255,255,255,.55);margin:16px 0 12px}
.contact__grid{display:grid;grid-template-columns:1.4fr 1fr;row-gap:4px;font-size:12px}
.contact__item{display:flex;align-items:center;gap:7px}
.contact__item--bold{font-weight:700}
.contact__item svg{width:11px;height:11px;fill:#fff;flex:none}
.back .url{left:38px;color:#fff}
.back .end-line{background:rgba(255,255,255,.7)}

/* outer spread — front cover */
.front{background:var(--paper-grey)}
.front .brand{left:68px;top:28px}
.front__rule{position:absolute;left:250px;right:38px;top:44px;height:1px;background:var(--red)}
.front .photo{left:40px;right:0;top:64px;height:520px;background:radial-gradient(ellipse at 55% 55%,#d9d3d0 0%,#ecebee 65%)}
.front__band{position:absolute;left:0;right:0;top:590px;bottom:0;background:var(--red-dark)}
.front__bar{position:absolute;right:0;top:578px;width:38px;height:12px;background:var(--bar)}
.front__card{position:absolute;left:40px;right:38px;top:480px;height:210px;background:var(--red);border-radius:26px 26px 0 0;padding:24px 26px}
.front__title{color:#fff;font-size:38px}
.front__sub{color:#fff;font-family:"Montserrat",sans-serif;font-weight:600;font-size:17.5px;margin-top:12px}
.front .url{left:68px;color:#fff}
.front .end-line{background:rgba(255,255,255,.7)}

/* inner spread — about */
.about{background:var(--paper)}
.about__rule{position:absolute;left:40px;right:40px;top:45px;height:1px;background:var(--red)}
.about .photo{left:0;top:0;width:492px;height:520px;border-bottom-right-radius:40px;background:linear-gradient(160deg,#f2f2f4 0%,#dfe4ea 55%,#c6d3e2 100%)}
.about__bar{position:absolute;left:0;top:524px;width:182px;height:12px;background:var(--bar)}
.about__title{position:absolute;left:38px;top:578px;color:var(--red);font-size:40px}
.about__divider{position:absolute;left:196px;top:585px;width:1px;height:104px;background:#bdbdbd}
.about__text{position:absolute;left:210px;top:584px;width:290px;font-size:11.3px;line-height:1.62;color:var(--text)}
.about .url{left:38px;color:var(--ink)}
.about .end-line{background:var(--red)}

/* inner spread — offers */
.offers{background:var(--paper)}
.offers__rule{position:absolute;left:40px;right:40px;top:45px;height:1px;background:var(--red)}
.offers__title{position:absolute;left:68px;top:68px;color:var(--ink);font-size:37px}
.perks{position:absolute;left:68px;top:136px;display:grid;grid-template-columns:150px 1fr;column-gap:22px;list-style:none;font-size:11px;line-height:1.55;color:var(--ink)}
.perks__col{display:flex;flex-direction:column;gap:8px}
.perk{display:flex;gap:9px;align-items:flex-start}
.perk svg{width:13px;height:13px;flex:none;margin-top:2px}
.offers__panel{position:absolute;left:40px;right:0;top:256px;bottom:0;background:var(--red);border-top-left-radius:52px}
.offers__bar{position:absolute;right:0;top:246px;width:182px;height:12px;background:var(--bar)}
.offers__head{position:absolute;left:76px;top:286px;color:#fff;font-size:37px}
.offers__intro{position:absolute;left:76px;top:392px;width:400px;color:#fff;font-size:10.5px;line-height:1.6}
.services{position:absolute;left:76px;top:460px;display:grid;grid-template-columns:repeat(3,130px);gap:13px}
.service{height:100px;background:#fff;border-radius:10px;display:flex;flex-direction:column;align-items:center;justify-content:center;gap:10px;font-family:"Montserrat",sans-serif;font-weight:700;font-size:11px;color:var(--ink)}
.service svg{width:36px;height:36px}
.offers .url{left:76px;color:#fff}
.offers .end-line{background:rgba(255,255,255,.7)}
</style>
</head>
<body>

<section class="spread spread--outer">
  <div class="page back">
    <div class="back__card"></div>
    <div class="back__bar"></div>
    <div class="brand brand--light"><span class="brand__dot"></span>WOLKENMUT</div>
    <h2 class="heading back__title">Kontaktieren<br>Sie uns<br>einfach</h2>
    <div class="back__dash"></div>
    <div class="contact">
      <p class="contact__name">Wolkenmut Haushaltshilfen &amp; Mehr<br>Carla Brenner</p>
      <div class="contact__rule"></div>
      <div class="contact__grid">
        <span class="contact__item contact__item--bold"><svg viewBox="0 0 24 24"><path d="M12 2a7 7 0 0 0-7 7c0 5 7 13 7 13s7-8 7-13a7 7 0 0 0-7-7zm0 9.5A2.5 2.5 0 1 1 12 6.5a2.5 2.5 0 0 1 0 5z"/></svg>Lindenweg 14, 70173 Musterstadt</span>
        <span class="contact__item"><svg viewBox="0 0 24 24"><path d="M2 5h20v14H2zM4 7v.5l8 5 8-5V7z"/></svg>info@wolkenmut.de</span>
        <span class="contact__item contact__item--bold"><svg viewBox="0 0 24 24"><path d="M6.6 10.8a15 15 0 0 0 6.6 6.6l2.2-2.2c.3-.3.7-.4 1-.2 1.1.4 2.3.6 3.6.6.6 0 1 .4 1 1V20c0 .6-.4 1-1 1A17 17 0 0 1 3 4c0-.6.4-1 1-1h3.5c.6 0 1 .4 1 1 0 1.3.2 2.5.6 3.6.1.3 0 .7-.2 1z"/></svg>0711 55501234</span>
        <span class="contact__item"><svg viewBox="0 0 24 24"><path d="M7 2h10a2 2 0 0 1 2 2v16a2 2 0 0 1-2 2H7a2 2 0 0 1-2-2V4a2 2 0 0 1 2-2zm0 3v13h10V5z"/></svg>0176 55509876</span>
      </div>
    </div>
    <span class="url">www.wolkenmut.de</span>
    <span class="end-line"></span>
  </div>

  <div class="page front">
    <div class="brand brand--red"><span class="brand__dot"></span>WOLKENMUT</div>
    <div class="front__rule"></div>
    <div class="photo" role="img" aria-label="Foto: Frau mit Staubwedel und Mann mit einem Arm voller Putzmittel und Handschuhe"></div>
    <div class="front__band"></div>
    <div class="front__bar"></div>
    <div class="front__card">
      <h1 class="heading front__title">Benötigen Sie<br>Hilfe im Haushalt?</h1>
      <p class="front__sub">Haushaltshilfen und Alltagsbegleiter</p>
    </div>
    <span class="url">www.wolkenmut.de</span>
    <span class="end-line"></span>
  </div>
</section>

<section class="spread spread--inner">
  <div class="page about">
    <div class="photo" role="img" aria-label="Foto: lächelnder Mann mit Wäschekorb voller Kleidung"></div>
    <div class="about__rule"></div>
    <div class="about__bar"></div>
    <h2 class="heading about__title">Über<br>Uns</h2>
    <div class="about__divider"></div>
    <p class="about__text">Wir bieten Haushaltshilfen und Alltagsbegleiter für Privathaushalte an. Unsere Hauptkundenklientel sind Pflegebedürftige Menschen denen eine Haushaltshilfe von der Pflegekasse zusteht. Weitere Kunden sind Familien und/oder Singlehaushalte, die eine Haushaltfshilfe benötigen.</p>
    <span class="url">www.wolkenmut.de</span>
    <span class="end-line"></span>
  </div>

  <div class="page offers">
    <div class="offers__rule"></div>
    <h2 class="heading offers__title">Unsere Vorteile</h2>
    <div class="perks">
      <div class="perks__col">
        <div class="perk"><svg viewBox="0 0 16 16"><circle cx="8" cy="8" r="6.5" fill="none" stroke="#c8102e" stroke-width="1.6"/><path d="M5 8.2l2.2 2.2L11.5 6" fill="none" stroke="#c8102e" stroke-width="1.8"/></svg><span>Abrechnung über den Entlastungsbetrag von mind. 125 €&nbsp; mtl. ab Pflegegrad 1 möglich</span></div>
      </div>
      <div class="perks__col">
        <div class="perk"><svg viewBox="0 0 16 16"><circle cx="8" cy="8" r="6.5" fill="none" stroke="#c8102e" stroke-width="1.6"/><path d="M5 8.2l2.2 2.2L11.5 6" fill="none" stroke="#c8102e" stroke-width="1.8"/></svg><span>Abrechnung mit allen Pflegekassen möglich</span></div>
        <div class="perk"><svg viewBox="0 0 16 16"><circle cx="8" cy="8" r="6.5" fill="none" stroke="#c8102e" stroke-width="1.6"/><path d="M5 8.2l2.2 2.2L11.5 6" fill="none" stroke="#c8102e" stroke-width="1.8"/></svg><span>Auch über die Verhinderungspflege</span></div>
        <div class="perk"><svg viewBox="0 0 16 16"><circle cx="8" cy="8" r="6.5" fill="none" stroke="#c8102e" stroke-width="1.6"/><path d="M5 8.2l2.2 2.2L11.5 6" fill="none" stroke="#c8102e" stroke-width="1.8"/></svg><span>Hilfe bei der Antragsstellung</span></div>
      </div>
    </div>
    <div class="offers__panel"></div>
    <div class="offers__bar"></div>
    <h2 class="heading offers__head">Die Vielfalt<br>unserer Angebote</h2>
    <p class="offers__intro">Den Alltag zu bewältigen kann eine echte Herausforderung sein.<br>Egal ob Sie Hilfe beim Einkaufen oder anderen alltäglichen<br>Aktivitäten benötigen, wir helfen gerne.</p>
    <div class="services">
      <div class="service"><svg viewBox="0 0 40 40"><path d="M4 20L18 7l14 13h-4v13H8V20z" fill="#c8102e"/><circle cx="29" cy="28" r="8" fill="#c8102e" stroke="#fff" stroke-width="2"/><path d="M25.5 28l2.5 2.5 4.5-4.5" fill="none" stroke="#fff" stroke-width="2"/></svg>Haushaltshilfe</div>
      <div class="service"><svg viewBox="0 0 40 40"><path d="M13 16l7-9 7 9" fill="none" stroke="#c8102e" stroke-width="2.5"/><path d="M4 15h32v5H4z" fill="#c8102e"/><path d="M7 20h26l-3 13H10z" fill="none" stroke="#c8102e" stroke-width="3"/><path d="M15 23v7M20 23v7M25 23v7" stroke="#c8102e" stroke-width="2.5"/></svg>Einkaufsservice</div>
      <div class="service"><svg viewBox="0 0 40 40"><rect x="7" y="4" width="26" height="32" rx="3" fill="#c8102e"/><circle cx="20" cy="22" r="8" fill="#fff"/><path d="M13 22a7 7 0 0 0 14 0" fill="#c8102e"/><circle cx="12" cy="9" r="1.6" fill="#fff"/><circle cx="17" cy="9" r="1.6" fill="#fff"/></svg>Wäscheservice</div>
      <div class="service"><svg viewBox="0 0 40 40"><path d="M33 5L20 20" stroke="#c8102e" stroke-width="3.5" stroke-linecap="round"/><path d="M17 17l7 7-4 4-10 8-6-6 9-10z" fill="#c8102e"/></svg>Kehrwoche</div>
      <div class="service"><svg viewBox="0 0 40 40"><rect x="8" y="5" width="24" height="28" fill="none" stroke="#c8102e" stroke-width="3.5"/><path d="M20 5v28M8 19h24" stroke="#c8102e" stroke-width="3.5"/><path d="M5 34h30" stroke="#c8102e" stroke-width="3"/></svg>Fensterreinigung</div>
      <div class="service"><svg viewBox="0 0 40 40"><path d="M5 9l3 3 5-5M5 20l3 3 5-5M5 31l3 3 5-5" fill="none" stroke="#c8102e" stroke-width="2.5"/><path d="M17 10h18M17 21h18M17 32h18" stroke="#c8102e" stroke-width="3.5"/></svg>Alltagsbegleitung</div>
    </div>
    <span class="url">www.wolkenmut.de</span>
    <span class="end-line"></span>
  </div>
</section>

</body>
</html>
```